Verlindo Magician

I want the business card for my business to give to people who watch that later I will be employed to show magic here is my website http://www.verlindoillusions.example/I want the interesting design , i am very opened for formal and informal, I watch a lot of design so don't stick to the common shape and form but i hope it can also be produced the thing to write on will be the same as in picture that i will upload , i also will upload the logo for you that so can be easy to useDenis CostilleMagicianMAGICIAN BALSAMO 17 rue des Tilleuls - 25000 BESANÇON contact@verlindoillusions.example tel. 0381 946 157 tel. 0674 219 503

```html
<!DOCTYPE html>
<html lang="fr">
<head>
<meta charset="utf-8">
<title>Verlindo Magician – Business Card</title>
<link href="https://fonts.googleapis.com/css2?family=Jost:wght@300;400;500&family=Lato:wght@400;700&display=swap" rel="stylesheet">
<style>
  :root {
    --red: #b3353a;
    --ink: #1a1a1a;
    --text: #333333;
    --paper: #ffffff;
    --backdrop: #e9e9e9;
    --figure: #141414;
  }
  * { margin: 0; padding: 0; box-sizing: border-box; }
  html, body { width: 1200px; height: 800px; overflow: hidden; }
  body {
    background: var(--backdrop);
    font-family: "Jost", sans-serif;
    position: relative;
  }
  .card {
    position: absolute;
    left: 300px;
    width: 600px;
    height: 348px;
    border-radius: 16px;
    overflow: hidden;
    background: var(--paper);
  }
  .card--front { top: 32px; }
  .card--back { top: 412px; }

  /* Front */
  .band-top {
    position: absolute; left: 0; top: 0; width: 100%; height: 81px;
    background: var(--red);
  }
  .band-bottom {
    position: absolute; left: 0; top: 299px; width: 100%; height: 49px;
    background: var(--red);
  }
  .wordmark {
    font-family: "Jost", sans-serif;
    font-weight: 300;
    letter-spacing: 1px;
    line-height: 1;
  }
  .front-wordmark {
    position: absolute; left: 28px; top: 20px;
    font-size: 38px; color: var(--paper);
  }
  .holder-name {
    position: absolute; left: 29px; top: 106px;
    font-family: "Lato", sans-serif; font-weight: 400;
    font-size: 22px; color: var(--red); letter-spacing: 0.2px;
  }
  .holder-role {
    position: absolute; left: 29px; top: 140px;
    font-size: 16px; font-weight: 400; color: var(--ink);
  }
  .contact-list {
    position: absolute; left: 29px; top: 172px;
    list-style: none;
  }
  .contact-list li {
    display: flex; align-items: center;
    height: 24.5px;
    font-size: 14.5px; color: var(--text); font-weight: 400;
  }
  .contact-list svg { width: 13px; height: 13px; margin-right: 9px; fill: var(--red); flex: none; }
  .business-label {
    position: absolute; left: 29px; top: 278px;
    font-size: 11.5px; font-weight: 500; color: var(--red); letter-spacing: 0.3px;
  }
  .address {
    position: absolute; left: 29px; top: 313px;
    font-size: 14.5px; color: var(--paper); font-weight: 400;
  }
  .portrait-front {
    position: absolute; left: 345px; top: 12px;
    width: 255px; height: 336px;
    border-radius: 60px 60px 0 0;
    background: linear-gradient(180deg, #2a2a2a 0%, var(--figure) 60%);
  }

  /* Back */
  .portrait-back {
    position: absolute; left: 204px; top: 28px;
    width: 186px; height: 231px;
    border-radius: 50px 50px 20px 20px;
    background: linear-gradient(180deg, #2a2a2a 0%, var(--figure) 60%);
  }
  .back-wordmark {
    position: absolute; left: 0; top: 268px; width: 100%;
    text-align: center; font-size: 38px; color: var(--ink);
  }
</style>
</head>
<body>

<section class="card card--front" aria-label="Card front">
  <div class="band-top"></div>
  <div class="band-bottom"></div>
  <div class="wordmark front-wordmark">VERLINDO</div>

  <h1 class="holder-name">MARC RAVOULET</h1>
  <p class="holder-role">MAGICIAN</p>

  <ul class="contact-list">
    <li><svg viewBox="0 0 16 16"><path d="M3.6 1.2l2.3 2.9-1.3 1.6c.9 2 2.6 3.8 4.7 4.7l1.6-1.3 2.9 2.3-1.5 2.9C6.9 14 2 9.1 1.5 2.7z"/></svg>0381 946 157</li>
    <li><svg viewBox="0 0 16 16"><path d="M1 6c1.5-2.5 12.5-2.5 14 0l-1 2-3-.7V5.8H5v1.5L2 8zM3 9h10l1 5H2z"/></svg>0674 219 503</li>
    <li><svg viewBox="0 0 16 16"><path d="M1 3h14v10H1zm1.5 1.5v.4L8 9l5.5-4.1v-.4z"/></svg>contact@verlindoillusions.example</li>
    <li><svg viewBox="0 0 16 16"><path d="M8 1a7 7 0 1 0 0 14A7 7 0 0 0 8 1zm0 1.5c.6 0 1.3 1.1 1.6 3H6.4C6.7 3.6 7.4 2.5 8 2.5zM2.6 7h2.3c0 .7 0 1.3.1 2H2.6a5.6 5.6 0 0 1 0-2zm3.8 0h3.2c.1.7.1 1.3 0 2H6.4c-.1-.7-.1-1.3 0-2zm4.7 0h2.3a5.6 5.6 0 0 1 0 2h-2.3c.1-.7.1-1.3 0-2zM6.4 10.5h3.2c-.3 1.9-1 3-1.6 3s-1.3-1.1-1.6-3z"/></svg>www.verlindoillusions.example</li>
  </ul>

  <p class="business-label">MAGICIAN VERLINDO</p>
  <p class="address">17 rue des Tilleuls - 25000 BESANÇON</p>

  <div class="portrait-front" role="img" aria-label="Black and white illustration of the magician in a dark jacket holding a playing card"></div>
</section>

<section class="card card--back" aria-label="Card back">
  <div class="portrait-back" role="img" aria-label="Black and white illustration of the magician in a dark jacket holding a playing card"></div>
  <div class="wordmark back-wordmark">VERLINDO</div>
</section>

</body>
</html>
```